Website design and coding for new consultancy company

I need to have a full website designed for a new consultancy business I'm trying to establish. It's called BrightPath consult. I need an English version to begin with, and then there should be a Danish version as well, but I'll translate that myself. Just be aware that I need two language versions. The consultancy field that I'm targeting is Leadership - and specialist development. I offer to facilitate corporate academies for global companies as well as specific workshops within leadership- or team development, strategy sessions, personal coaching and facilitation of D&I (Diversity and inclusion) workshops. BTW my logo is not in high resolution - I need that as well.

Target Market(s)

Larger companies that has a need for developing their inhouse leadership capabilities or that wants to develop their specialists to take on more responsibility.

Industry/Entity Type

Consultancy business

Coding

Coded - Design and coding required

Number of Pages Required

5+ page

Requirements
Must have
• Introduction site with a catch phrase. Book a meeting. Services that's beeing offered. Blog site with white papers etc. Language toggle (Danish/English). Cases/testimonials. About site. Contact site.

```html
<!DOCTYPE html>
<html lang="en">
<head>
<meta charset="utf-8">
<title>BrightPath Consult – Leadership &amp; Specialist Development</title>
<link href="https://fonts.googleapis.com/css2?family=Lato:wght@400;700;900&display=swap" rel="stylesheet">
<style>
:root{
  --blue:#2a86d0;
  --blue-deep:#2f87cf;
  --ink:#111418;
  --text:#2b2f33;
  --muted:#4a4f55;
  --pale:#e8f3fb;
  --white:#ffffff;
  --footer:#0b0b0b;
}
*{box-sizing:border-box;margin:0;padding:0}
html,body{width:1200px;height:3495px;overflow:hidden}
body{font-family:'Lato',sans-serif;color:var(--text);background:var(--white);position:relative}
.abs{position:absolute}
a{color:inherit;text-decoration:none}

/* header */
.site-header{position:absolute;left:0;top:0;width:1200px;height:85px;background:var(--white);box-shadow:0 2px 6px rgba(0,0,0,.06);z-index:2}
.brand{position:absolute;left:60px;top:22px;display:flex;align-items:center;gap:12px;font-weight:900;font-size:34px;letter-spacing:1px;color:var(--ink)}
.brand-square{width:30px;height:30px;background:var(--blue)}
.main-nav{position:absolute;top:32px;font-size:17px;color:var(--text)}
.main-nav.active{color:var(--blue);font-weight:700}
.btn{display:flex;align-items:center;justify-content:center;gap:8px;background:var(--blue);color:var(--white);font-size:16px;position:absolute}
.btn svg{width:14px;height:14px}

/* hero */
.hero{position:absolute;left:0;top:85px;width:1200px;height:509px;background:linear-gradient(90deg,#d9dde6 0%,#dfe2ea 40%,#c9ced8 70%,#aeb6c2 100%)}
.hero-photo{position:absolute;right:0;top:0;width:640px;height:509px;background:linear-gradient(160deg,#cfd4de 0%,#a9b1bd 55%,#7f8896 100%)}
.hero-title{position:absolute;left:60px;top:116px;font-size:48px;font-weight:900;line-height:55px;color:var(--white)}
.hero-title span{color:var(--blue)}
.hero-text{position:absolute;left:60px;top:246px;width:470px;font-size:16px;line-height:24px;color:#2a2d31}

/* about */
.about{position:absolute;left:0;top:594px;width:1200px;height:588px;background:var(--pale)}
.accent-bar{position:absolute;height:3px;background:var(--blue)}
.h2{font-size:35px;font-weight:900;color:var(--ink);position:absolute}
.h2 span{color:var(--blue)}
.point{position:absolute;left:663px;border-left:3px solid var(--blue);padding-left:18px}
.point h3{font-size:18px;font-weight:700;color:var(--ink);line-height:22px}
.point p{font-size:13px;color:var(--muted);margin-top:6px}

/* offer */
.offer-item{position:absolute;width:260px}
.offer-item h3{font-size:19px;font-weight:700;color:var(--ink)}
.offer-item p{font-size:13px;line-height:18px;color:var(--muted);margin-top:10px}
.offer-item.right-aligned{text-align:right}
.icon-ring{position:absolute;width:82px;height:82px;border-radius:50%;background:var(--white);border:2px solid #e1e6ec;box-shadow:0 2px 6px rgba(0,0,0,.08);display:flex;align-items:center;justify-content:center}
.icon-ring svg{width:46px;height:46px}

/* why */
.why{position:absolute;left:0;top:1850px;width:1200px;height:615px;background:var(--blue-deep)}
.why .h2{color:var(--white)}
.feature-icon{position:absolute;width:79px;height:78px}
.feature-icon .frame{position:absolute;left:0;top:8px;width:72px;height:70px;border-left:3px solid var(--white);border-bottom:3px solid var(--white)}
.feature-icon .tile{position:absolute;left:8px;top:0;width:71px;height:70px;background:var(--white);display:flex;align-items:center;justify-content:center}
.feature-icon svg{width:40px;height:40px}
.feature-title{position:absolute;left:210px;font-size:20px;font-weight:700;color:var(--white)}
.feature-text{position:absolute;left:210px;font-size:13px;line-height:18px;color:var(--white);width:330px}

/* blog */
.post{position:absolute;top:2683px;width:432px}
.post-image{width:432px;height:232px}
.post-meta{font-size:14px;color:var(--muted);margin-top:24px}
.post-title{font-size:19px;font-weight:700;line-height:26px;color:var(--ink);margin-top:18px}
.post-text{font-size:13px;line-height:18px;color:var(--muted);margin-top:12px}
.slider-btn{position:absolute;top:3139px;width:36px;height:36px;border-radius:50%;display:flex;align-items:center;justify-content:center}

/* footer */
.site-footer{position:absolute;left:0;top:3258px;width:1200px;height:237px;background:var(--footer);color:var(--white)}
.footer-brand{position:absolute;left:0;width:1200px;top:64px;display:flex;justify-content:center;align-items:center;gap:14px;font-weight:900;font-size:40px;letter-spacing:1px}
.footer-nav{position:absolute;left:0;width:1200px;top:150px;display:flex;justify-content:center;gap:38px;font-size:17px}
.footer-rule{position:absolute;left:111px;top:186px;width:978px;height:1px;background:#cfcfcf}
.copyright{position:absolute;left:0;width:1200px;top:201px;text-align:center;font-size:12px;color:#cfcfcf}
</style>
</head>
<body>

<header class="site-header">
  <div class="brand"><span class="brand-square"></span>BRIGHTPATH</div>
  <a class="main-nav active" style="left:569px">Home</a>
  <a class="main-nav" style="left:652px">About</a>
  <a class="main-nav" style="left:734px">Services</a>
  <a class="main-nav" style="left:831px">Resources</a>
  <a class="main-nav" style="left:943px">En <svg width="10" height="8" viewBox="0 0 10 8"><path d="M1 2l4 4 4-4" fill="none" stroke="#2b2f33" stroke-width="1.5"/></svg></a>
  <a class="btn" style="left:1007px;top:26px;width:139px;height:34px">
    <svg viewBox="0 0 14 14"><path d="M2 2l5 5-5 5M7 2l5 5-5 5" fill="none" stroke="#fff" stroke-width="1.8"/></svg>Contact Us</a>
</header>

<section class="hero">
  <div class="hero-photo" role="img" aria-label="Photo of two smiling business colleagues reviewing a tablet in a bright office"></div>
  <h1 class="hero-title"><span>Where Leaders Grow &amp;</span><br>Organizations Thrive.</h1>
  <p class="hero-text">At BrightPath Consult, we help organizations unlock their leadership potential, build stronger teams, and create inclusive workplaces where people thrive.</p>
  <a class="btn" style="left:60px;top:346px;width:202px;height:36px">
    <svg viewBox="0 0 14 14"><path d="M2 2l5 5-5 5M7 2l5 5-5 5" fill="none" stroke="#fff" stroke-width="1.8"/></svg>Explore Our Services</a>
</section>

<section class="about">
  <div class="abs" style="left:129px;top:351px;width:171px;height:151px;background:var(--blue)"></div>
  <div class="abs" role="img" aria-label="Portrait photo of a confident businessman in front of office buildings" style="left:159px;top:104px;width:405px;height:370px;background:linear-gradient(150deg,#7d8792 0%,#4d5560 55%,#2c3139 100%)"></div>

  <div class="accent-bar" style="left:663px;top:101px;width:82px"></div>
  <h2 class="h2" style="left:663px;top:110px"><span>About</span> BrightPath</h2>
  <p class="abs" style="left:663px;top:172px;width:437px;font-size:15.5px;line-height:26px;text-align:justify;color:var(--text)">BrightPath Consult is a leadership and specialist development consultancy. We partner with global companies to design &amp; facilitate programs that strengthen leadership capability, align strategy, and foster growth across all levels of the organization.</p>
  <div class="point" style="top:305px"><h3>Human-centered development</h3><p>Focusing On People First.</p></div>
  <div class="point" style="top:368px"><h3>Global perspective</h3><p>Experience with diverse teams and international organizations.</p></div>
  <div class="point" style="top:432px"><h3>Sustainable impact</h3><p>Creating long-term change, not quick fixes.</p></div>
</section>

<section class="offer">
  <div class="accent-bar" style="left:560px;top:1268px;width:80px"></div>
  <h2 class="h2" style="left:0;width:1200px;text-align:center;top:1275px"><span>What</span> We Offer</h2>
  <p class="abs" style="left:0;width:1200px;top:1340px;text-align:center;font-size:15.5px;line-height:26px">At BrightPath Consult, we design tailored programs and workshops that strengthen leadership,<br>enhance collaboration, and drive measurable results.</p>

  <div class="offer-item right-aligned" style="left:144px;top:1440px"><h3>Corporate Academies</h3><p>Long-term development programs for<br>leaders and specialists in global</p></div>
  <div class="icon-ring" style="left:432px;top:1436px">
    <svg viewBox="0 0 46 46"><rect x="11" y="8" width="24" height="14" fill="#2a86d0"/><circle cx="23" cy="30" r="10" fill="none" stroke="#2a86d0" stroke-width="4"/><circle cx="23" cy="30" r="3" fill="#2a86d0"/></svg></div>

  <div class="icon-ring" style="left:693px;top:1436px">
    <svg viewBox="0 0 46 46"><circle cx="23" cy="10" r="5" fill="#2a86d0"/><path d="M23 17c-5 0-8 6-8 14h16c0-8-3-14-8-14z" fill="#2a86d0"/><path d="M6 12c2 12 6 20 12 26M40 12c-2 12-6 20-12 26" fill="none" stroke="#2a86d0" stroke-width="3"/></svg></div>
  <div class="offer-item" style="left:801px;top:1440px"><h3>Executive Coaching</h3><p>One-to-one coaching for leaders and<br>high-potential talents.</p></div>

  <div class="offer-item right-aligned" style="left:76px;top:1569px"><h3>Strategy Sessions</h3><p>Facilitated sessions to align vision,<br>goals, and execution at the executive</p></div>
  <div class="icon-ring" style="left:363px;top:1564px">
    <svg viewBox="0 0 46 46"><rect x="18" y="6" width="22" height="16" rx="2" fill="#2a86d0"/><rect x="5" y="20" width="22" height="15" rx="1" fill="none" stroke="#2a86d0" stroke-width="3"/><circle cx="14" cy="26" r="3" fill="#2a86d0"/><path d="M12 40h14" stroke="#2a86d0" stroke-width="3"/></svg></div>

  <div class="icon-ring" style="left:762px;top:1564px">
    <svg viewBox="0 0 46 46"><path d="M34 4l2.5 5 5.5.8-4 3.9 1 5.5-5-2.6-5 2.6 1-5.5-4-3.9 5.5-.8z" fill="#2a86d0"/><circle cx="23" cy="24" r="4" fill="#2a86d0"/><circle cx="11" cy="30" r="4" fill="#2a86d0"/><circle cx="35" cy="30" r="4" fill="#2a86d0"/><path d="M4 42c1-6 13-6 14 0M16 38c1-7 13-7 14 0M28 42c1-6 13-6 14 0" fill="#2a86d0"/></svg></div>
  <div class="offer-item" style="left:870px;top:1569px"><h3>Inclusive Leadership</h3><p>Creating inclusive, culturally aware,<br>and equitable workplaces.</p></div>

  <a class="btn" style="left:506px;top:1729px;width:188px;height:35px">
    <svg viewBox="0 0 14 14"><path d="M2 2l5 5-5 5M7 2l5 5-5 5" fill="none" stroke="#fff" stroke-width="1.8"/></svg>View All Services</a>
</section>

<section class="why">
  <div class="accent-bar" style="left:111px;top:86px;width:82px;background:var(--white)"></div>
  <h2 class="h2" style="left:111px;top:94px">Why Choose Us</h2>
  <p class="abs" style="left:111px;top:156px;width:426px;font-size:15.5px;line-height:26px;color:var(--white);text-align:justify">Choosing the right partner for leadership and organizational development makes all the difference. At BrightPath Consult, we combine global expertise with a human-centered approach to create lasting impact.</p>

  <div class="feature-icon" style="left:111px;top:296px"><div class="frame"></div><div class="tile">
    <svg viewBox="0 0 40 40"><circle cx="12" cy="10" r="5" fill="#2a86d0"/><path d="M4 28c0-7 4-11 8-11s8 4 8 11z" fill="#2a86d0"/><rect x="20" y="24" width="14" height="10" fill="#2a86d0"/><path d="M30 4l1.5 3 3 .5-2.2 2 .6 3-2.9-1.5-2.9 1.5.6-3-2.2-2 3-.5z" fill="#2a86d0"/></svg></div></div>
  <h3 class="feature-title" style="top:297px">Proven Experience</h3>
  <p class="feature-text" style="top:328px">Trusted by international companies to develop<br>leaders and teams at all levels.</p>

  <div class="feature-icon" style="left:111px;top:406px"><div class="frame"></div><div class="tile">
    <svg viewBox="0 0 40 40"><circle cx="20" cy="14" r="10" fill="none" stroke="#2a86d0" stroke-width="3"/><path d="M10 14h20M20 4c-4 5-4 15 0 20M20 4c4 5 4 15 0 20" stroke="#2a86d0" stroke-width="2" fill="none"/><path d="M3 24c4 0 9 10 17 10s13-10 17-10" fill="none" stroke="#2a86d0" stroke-width="3"/></svg></div></div>
  <h3 class="feature-title" style="top:406px">Sustainable Impact</h3>
  <p class="feature-text" style="top:437px">We focus on measurable results that drive long-term<br>growth, not quick fixes.</p>

  <div class="abs" role="img" aria-label="Photo of a cheerful team meeting around a laptop in a modern office" style="left:683px;top:86px;width:406px;height:392px;background:linear-gradient(150deg,#b9c3cf 0%,#8795a6 50%,#5d6a7b 100%)"></div>
  <div class="abs" style="left:589px;top:332px;width:228px;height:204px;background:var(--blue-deep)"></div>
  <div class="abs" role="img" aria-label="Photo of wooden letter blocks spelling lead being turned into learn" style="left:597px;top:340px;width:212px;height:188px;background:linear-gradient(180deg,#b7c98a 0%,#c9cfbf 60%,#e8e6e0 100%)"></div>
</section>

<section class="blog">
  <div class="accent-bar" style="left:560px;top:2552px;width:82px"></div>
  <h2 class="h2" style="left:0;width:1200px;text-align:center;top:2559px"><span>Latest</span> Blog</h2>
  <p class="abs" style="left:0;width:1200px;top:2623px;text-align:center;font-size:15.5px">Global expertise with a human-centered approach to leadership development.</p>

  <article class="post" style="left:111px">
    <div class="post-image" role="img" aria-label="Photo of colleagues collaborating over documents at a meeting table" style="background:linear-gradient(135deg,#c6d2de 0%,#8fa1b3 55%,#5e6f80 100%)"></div>
    <p class="post-meta">By Admin &nbsp;&nbsp;|&nbsp;&nbsp; 12<sup>th</sup> Aug 2025</p>
    <h3 class="post-title">Lorem ipsum dolor sit amet, consectetur adipisc elit, sed do eiusmod tempor</h3>
    <p class="post-text">Lorem ipsum dolor sit amet, consectetur adipiscing elit, sed do eiusmod tempor incididunt ut labore et dolore magna aliqua. Ut enim ad minim veniam, quis nostrud exercitation</p>
  </article>
  <article class="post" style="left:572px">
    <div class="post-image" role="img" aria-label="Illustration of a compass needle pointing to the word leadership" style="background:linear-gradient(135deg,#dfe5ec 0%,#aebccb 60%,#8a9cb0 100%)"></div>
    <p class="post-meta">By Admin &nbsp;&nbsp;|&nbsp;&nbsp; 12<sup>th</sup> Aug 2025</p>
    <h3 class="post-title">Lorem ipsum dolor sit amet, consectetur adipisc elit, sed do eiusmod tempor</h3>
    <p class="post-text">Lorem ipsum dolor sit amet, consectetur adipiscing elit, sed do eiusmod tempor incididunt ut labore et dolore magna aliqua. Ut enim ad minim veniam, quis nostrud exercitation</p>
  </article>
  <article class="post" style="left:1033px">
    <div class="post-image" role="img" aria-label="Photo of a smiling professional woman in front of a sticky-note wall" style="background:linear-gradient(135deg,#e0b35a 0%,#d9c7a8 50%,#a9b6c4 100%)"></div>
    <p class="post-meta">By Admin &nbsp;&nbsp;|&nbsp;&nbsp; 12<sup>th</sup> Aug 2025</p>
    <h3 class="post-title">Lorem ipsum dolor sit amet, consectetur adipisc elit, sed do eiusmod tempor</h3>
    <p class="post-text">Lorem ipsum dolor sit amet, consectetur adipiscing elit, sed do eiusmod tempor incididunt ut labore et dolore magna aliqua. Ut enim ad minim veniam, quis nostrud exercitation</p>
  </article>

  <a class="slider-btn" style="left:556px;border:2px solid var(--ink)">
    <svg width="12" height="14" viewBox="0 0 12 14"><path d="M8 2L3 7l5 5" fill="none" stroke="#111418" stroke-width="2"/></svg></a>
  <a class="slider-btn" style="left:608px;background:var(--blue)">
    <svg width="12" height="14" viewBox="0 0 12 14"><path d="M4 2l5 5-5 5" fill="none" stroke="#fff" stroke-width="2"/></svg></a>
</section>

<footer class="site-footer">
  <div class="footer-brand"><span style="width:34px;height:34px;background:var(--white)"></span>BRIGHTPATH</div>
  <nav class="footer-nav"><a>Home</a><a>About</a><a>Services</a><a>Resources</a><a>Contact Us</a></nav>
  <div class="footer-rule"></div>
  <p class="copyright">Copyright © 2025 BrightPath. All rights reserved.</p>
</footer>

</body>
</html>
```